Stationary for a property rental company
Bellcombe Rentals
Stationary for a property rental company - Real Estate
Creative Brief
Simple
Greta Halvick
Owner
PO Box 7419 Drayford Falls, VT 05981
greta@bellcomberentals.example
www.bellcomberentals.example
Please use similar colors that are found in the Logo.
Use emblem for the back of the card

```html
<!DOCTYPE html>
<html lang="en">
<head>
<meta charset="utf-8">
<title>Bellcombe Rentals – Business Card</title>
<link rel="stylesheet" href="https://fonts.googleapis.com/css2?family=Crimson+Text:wght@400;600&display=swap">
<style>
  :root {
    --bg: #e9ebee;
    --card-white: #ffffff;
    --steel-light: #5b8aa5;
    --steel-dark: #3a6680;
    --navy: #2d4a70;
    --teal-name: #3d6f8c;
    --ink: #3a3f45;
    --icon-band: #4f7f9c;
  }
  * { margin: 0; padding: 0; box-sizing: border-box; }
  html, body {
    width: 1200px; height: 901px; overflow: hidden;
    background: var(--bg);
    font-family: "Crimson Text", Georgia, serif;
  }
  .stage {
    width: 1200px; height: 901px;
    display: flex; flex-direction: column;
    align-items: center; justify-content: center; gap: 28px;
  }
  .card {
    position: relative;
    width: 720px; height: 411px;
    border-radius: 24px;
    overflow: hidden;
    box-shadow: 0 6px 18px rgba(0,0,0,0.18);
  }
  /* Back */
  .card-back {
    background: linear-gradient(160deg, var(--steel-light), var(--steel-dark));
    display: flex; align-items: center; justify-content: center;
  }
  .emblem {
    width: 230px; height: 230px; border-radius: 50%;
    border: 3px solid rgba(255,255,255,0.85);
    display: flex; align-items: center; justify-content: center;
    text-align: center;
  }
  .emblem-name {
    color: #ffffff; font-weight: 600; font-size: 30px; line-height: 1.1;
    letter-spacing: 1px;
  }
  /* Front */
  .card-front { background: var(--card-white); }
  .brand {
    position: absolute; left: 62px; top: 62px;
    display: flex; align-items: center; gap: 12px;
  }
  .brand-dot { width: 14px; height: 14px; border-radius: 50%; background: var(--navy); }
  .brand-name {
    color: var(--navy); font-weight: 600; font-size: 38px;
    letter-spacing: 1px; line-height: 1;
  }
  .address {
    position: absolute; left: 62px; top: 210px;
    color: var(--ink); font-size: 18px; line-height: 1.2;
  }
  .icon-band {
    position: absolute; left: 0; top: 270px;
    width: 24px; height: 84px; background: var(--icon-band);
    display: flex; flex-direction: column; align-items: center;
    justify-content: space-around; padding: 6px 0;
  }
  .icon-band svg { width: 13px; height: 13px; }
  .contacts {
    position: absolute; left: 62px; top: 274px;
    list-style: none; color: var(--ink); font-size: 17px; line-height: 26px;
  }
  .person {
    position: absolute; right: 70px; top: 188px; text-align: right;
  }
  .person-name { color: var(--teal-name); font-weight: 600; font-size: 24px; line-height: 1.1; }
  .person-title { color: var(--ink); font-size: 16px; }
</style>
</head>
<body>
<main class="stage">
  <section class="card card-back" aria-label="Card back">
    <div class="emblem">
      <span class="emblem-name">Bellcombe<br>Rentals</span>
    </div>
  </section>

  <section class="card card-front" aria-label="Card front">
    <div class="brand">
      <span class="brand-dot"></span>
      <span class="brand-name">BELLCOMBE RENTALS</span>
    </div>

    <p class="address">PO Box 7419<br>Drayford Falls, VT 05981</p>

    <div class="icon-band" aria-hidden="true">
      <svg viewBox="0 0 16 16"><path fill="#fff" d="M4 1l3 3-2 2c1 2 3 4 5 5l2-2 3 3-2 3C7 15 1 9 1 3z"/></svg>
      <svg viewBox="0 0 16 16"><rect x="1" y="3" width="14" height="10" fill="none" stroke="#fff" stroke-width="1.6"/><path d="M1 3l7 6 7-6" fill="none" stroke="#fff" stroke-width="1.6"/></svg>
      <svg viewBox="0 0 16 16"><circle cx="8" cy="8" r="6.5" fill="none" stroke="#fff" stroke-width="1.5"/><path d="M1.5 8h13M8 1.5c-3 4-3 9 0 13M8 1.5c3 4 3 9 0 13" fill="none" stroke="#fff" stroke-width="1.2"/></svg>
    </div>

    <ul class="contacts">
      <li>802.555.0147</li>
      <li>greta@bellcomberentals.example</li>
      <li>www.bellcomberentals.example</li>
    </ul>

    <div class="person">
      <p class="person-name">Greta Halvick</p>
      <p class="person-title">Owner</p>
    </div>
  </section>
</main>
</body>
</html>
```